professional business card design for technology company

We are a small technology consulting firm, specialising in consulting based around Cloud and Managed services. Our colour scheme is yellow, blue and white, as you can see in the logos. Although we are based in melbourne australia, due to the nature of our work, our clients can be located anywhere. We are looking for a clean, professional, positive look - similar to our company logo

Target Market(s)

small business

Industry/Entity Type

Business

Contact Information for Business Card

eye catching, designed to incorporate some level of raised printing. Must contain website address, phone number, name and job title

Requirements
Must have
• Logo (attached) - use of the same colour scheme

```html
<!DOCTYPE html>
<html lang="en">
<head>
<meta charset="UTF-8">
<title>Norvane Business Card</title>
<link href="https://fonts.googleapis.com/css2?family=Lato:wght@400;700;900&display=swap" rel="stylesheet">
<style>
  :root {
    --backdrop: #2a2a2a;
    --card-white: #fafafa;
    --card-dark: #4a4a4a;
    --brand-blue: #2f95c8;
    --brand-yellow: #f2cf1d;
    --ink-grey: #444444;
    --ink-soft: #333333;
    --line-white: #ffffff;
  }
  * { margin: 0; padding: 0; box-sizing: border-box; }
  html, body { width: 1200px; height: 873px; overflow: hidden; }
  body {
    background: var(--backdrop);
    font-family: "Lato", Arial, sans-serif;
    position: relative;
  }
  .card {
    position: absolute;
    width: 540px;
    height: 308px;
    top: 282px;
    overflow: hidden;
    box-shadow: 0 12px 30px rgba(0,0,0,0.45);
  }
  .card--back { left: 40px; background: var(--card-dark); }
  .card--front { left: 620px; background: var(--card-white); }

  .wordmark {
    position: absolute;
    display: flex;
    align-items: center;
    gap: 16px;
  }
  .wordmark__dot {
    width: 50px; height: 50px;
    border-radius: 50%;
    background: var(--brand-yellow);
    flex: none;
  }
  .wordmark__name {
    font-weight: 900;
    font-size: 56px;
    letter-spacing: -1px;
    line-height: 1;
  }
  .card--front .wordmark { left: 110px; top: 52px; }
  .card--front .wordmark__name { color: var(--ink-grey); }

  .card--back .wordmark { left: 120px; top: 104px; }
  .card--back .wordmark__name { color: var(--line-white); font-size: 52px; }
  .tagline {
    position: absolute;
    left: 188px; top: 172px;
    color: var(--brand-blue);
    font-weight: 700;
    font-size: 13px;
    letter-spacing: 4px;
  }

  .band {
    position: absolute;
    left: 0; right: 0; bottom: 0;
    height: 150px;
    background: var(--brand-blue);
  }
  .band__rule {
    position: absolute;
    left: 0; right: 0;
    height: 3px;
    background: var(--brand-blue);
  }
  .band__rule--one { bottom: 164px; }
  .band__rule--two { bottom: 156px; }
  .band__inner-rule {
    position: absolute;
    left: 0; right: 0; top: 6px;
    height: 2px;
    background: var(--line-white);
  }

  .person {
    position: absolute;
    left: 32px; bottom: 26px;
  }
  .person__name {
    color: var(--line-white);
    font-weight: 700;
    font-size: 19px;
  }
  .person__role {
    color: var(--ink-soft);
    font-weight: 700;
    font-size: 12px;
    letter-spacing: 0.5px;
    margin-top: 3px;
  }

  .contacts {
    position: absolute;
    left: 300px; top: 20px;
    list-style: none;
  }
  .contacts__item {
    display: flex;
    align-items: center;
    gap: 8px;
    color: var(--ink-soft);
    font-size: 14px;
    line-height: 20px;
    margin-bottom: 6px;
    white-space: nowrap;
  }
  .contacts__icon {
    width: 20px; height: 20px;
    background: var(--line-white);
    display: flex; align-items: center; justify-content: center;
    flex: none;
  }
  .contacts__icon svg { width: 14px; height: 14px; }
</style>
</head>
<body>

  <section class="card card--back" aria-label="Card back">
    <div class="wordmark">
      <span class="wordmark__dot"></span>
      <span class="wordmark__name">Norvane</span>
    </div>
    <p class="tagline">YOUR SLOGAN / TAGLINE HERE</p>
  </section>

  <section class="card card--front" aria-label="Card front">
    <div class="wordmark">
      <span class="wordmark__dot"></span>
      <span class="wordmark__name">Norvane</span>
    </div>

    <div class="band__rule band__rule--one"></div>
    <div class="band__rule band__rule--two"></div>
    <div class="band">
      <div class="band__inner-rule"></div>

      <div class="person">
        <p class="person__name">Liam Hartley</p>
        <p class="person__role">MANAGING DIRECTOR</p>
      </div>

      <ul class="contacts">
        <li class="contacts__item">
          <span class="contacts__icon">
            <svg viewBox="0 0 14 14"><rect x="3.5" y="1" width="7" height="12" rx="1" fill="none" stroke="#333" stroke-width="1.3"/><circle cx="7" cy="11" r="0.8" fill="#333"/></svg>
          </span>
          (555) 201-4870
        </li>
        <li class="contacts__item">
          <span class="contacts__icon">
            <svg viewBox="0 0 14 14"><path d="M2 5 Q7 1 12 5 L10.5 6.5 L9 5.2 L5 5.2 L3.5 6.5 Z" fill="#333"/><rect x="3" y="7" width="8" height="5" rx="1" fill="#333"/></svg>
          </span>
          01632 960 418
        </li>
        <li class="contacts__item">
          <span class="contacts__icon">
            <svg viewBox="0 0 14 14"><rect x="1.5" y="3" width="11" height="8" fill="none" stroke="#333" stroke-width="1.3"/><path d="M1.5 3 L7 8 L12.5 3" fill="none" stroke="#333" stroke-width="1.3"/></svg>
          </span>
          hello@norvanecloud.com
        </li>
        <li class="contacts__item">
          <span class="contacts__icon">
            <svg viewBox="0 0 14 14"><circle cx="7" cy="7" r="5.5" fill="none" stroke="#333" stroke-width="1.2"/><ellipse cx="7" cy="7" rx="2.4" ry="5.5" fill="none" stroke="#333" stroke-width="1"/><path d="M1.5 7 H12.5" stroke="#333" stroke-width="1"/></svg>
          </span>
          www.norvanecloud.com
        </li>
      </ul>
    </div>
  </section>

</body>
</html>
```